Business Report Cover

We need a revamped quarterly report cover to send to our clients. We asset manage commercial and residential properties throughout the the United States. We use a .pdf version of a cover that we've used for years but would like a fresh updated look for 2018. The cover should include our company logo (KOV Enterprises) and a photo of the property as well as the Quarter/Year of the report.

```html
<!DOCTYPE html>
<html lang="en">
<head>
<meta charset="utf-8">
<title>KOV Enterprises — 2018 Quarterly Operating Report, 1st Quarter</title>
<link rel="stylesheet" href="https://fonts.googleapis.com/css2?family=Montserrat:wght@800&family=Questrial&display=swap">
<style>
  :root {
    --backdrop: #e9e5df;
    --paper: #ffffff;
    --ink: #111111;
    --charcoal: #2c2c2c;
    --green-deep: #17783f;
    --green-band: #1f8048;
    --green-panel: #3a8c5f;
    --photo-sky: #d9dde2;
    --photo-mid: #7d6f68;
    --photo-ground: #3c3d40;
    --on-green: #ffffff;
  }
  * { margin: 0; padding: 0; box-sizing: border-box; }
  html, body {
    width: 1200px;
    height: 1200px;
    overflow: hidden;
    background: var(--backdrop);
  }
  .report-cover {
    position: absolute;
    left: 190px;
    top: 20px;
    width: 820px;
    height: 1160px;
    background: var(--paper);
    box-shadow: 0 2px 10px rgba(0,0,0,0.12);
  }
  .report-cover svg { display: block; width: 100%; height: 100%; }
  .brand-name { font-family: "Montserrat", sans-serif; font-weight: 800; fill: var(--ink); }
  .year { font-family: "Questrial", sans-serif; fill: var(--green-deep); }
  .report-title { font-family: "Questrial", sans-serif; fill: var(--ink); letter-spacing: -0.5px; }
  .property-address { font-family: "Questrial", sans-serif; fill: var(--on-green); }
  .accent-dark { fill: var(--charcoal); }
  .accent-band { fill: var(--green-band); opacity: 0.9; }
  .accent-panel { fill: var(--green-panel); opacity: 0.92; }
  .title-rule { stroke: var(--green-deep); stroke-width: 5; }
</style>
</head>
<body>
  <main class="report-cover">
    <svg viewBox="0 0 978 1383" xmlns="http://www.w3.org/2000/svg">
      <defs>
        <linearGradient id="propertyTones" x1="0" y1="0" x2="0" y2="1">
          <stop offset="0" stop-color="var(--photo-sky)"/>
          <stop offset="0.45" stop-color="#b9b7b5"/>
          <stop offset="0.62" stop-color="var(--photo-mid)"/>
          <stop offset="1" stop-color="var(--photo-ground)"/>
        </linearGradient>
      </defs>

      <!-- Company name -->
      <g class="brand">
        <text class="brand-name" x="65" y="146" font-size="92" letter-spacing="-2">KOV</text>
        <text class="brand-name" x="66" y="180" font-size="20" letter-spacing="8.5">ENTERPRISES</text>
      </g>

      <!-- Property photo area -->
      <polygon class="property-photo" role="img"
               aria-label="Photo of the managed retail property: a convenience store with a fuel canopy, pumps and landscaped parking lot under a cloudy sky"
               points="238,270 978,25 978,813 238,1043" fill="url(#propertyTones)"/>

      <!-- Geometric accents -->
      <polygon class="accent-band" points="386,173 978,25 978,133 386,276"/>
      <polygon class="accent-dark" points="541,106 978,0 978,38 541,148"/>
      <polygon class="accent-panel" points="0,883 386,773 386,1383 0,1383"/>
      <polygon class="accent-dark" points="155,506 204,498 204,1051 155,1063"/>

      <!-- Report title -->
      <text class="year" x="933" y="1083" text-anchor="end" font-size="124" letter-spacing="-3">2018</text>
      <line class="title-rule" x1="433" y1="1115" x2="978" y2="1115"/>
      <text class="report-title" x="935" y="1164" text-anchor="end" font-size="37">QUARTERLY OPERATING REPORT</text>
      <text class="report-title" x="926" y="1208" text-anchor="end" font-size="37">1ST QUARTER</text>

      <!-- Property address -->
      <g class="property-address" font-size="22">
        <text x="85" y="1273">Harbor Corner Market</text>
        <text x="85" y="1305">1470 NE Cedar Park Way</text>
        <text x="85" y="1336">Ridgefield, WA 98604</text>
      </g>
    </svg>
  </main>
</body>
</html>
```